Ward Compass Business Card Design*

We need a business card design for our company Ward Compass. Our company is specialized in providing online consulting services regarding medical institutions, hospitals and doctors. We work with patients worldwide looking to choose between healthcare providers. We have a website you may use as a reference, where we list doctors and clinics worldwide. So we target Medical providers as well as patients worldwide.
Target Market(s)
Medical Providers and patients around the world
Industry/Entity Type
Medical
Contact Information for Business Card
Salwa Kettani
CEO
+90 612 348 2175
info@wardcompass.example
www.wardcompass.example
14 Annakhil 7 H.R.B. Rabat, Morocco
Requirements
Must have
- Company logo/name on one full side, personal info and smaller logo and company name on the other side.
Nice to have
- Smart and elegant design

```html
<!DOCTYPE html>
<html lang="en">
<head>
<meta charset="utf-8">
<title>Ward Compass Business Card</title>
<link href="https://fonts.googleapis.com/css2?family=Lato:wght@400;700&display=swap" rel="stylesheet">
<style>
  :root {
    --backdrop: #e3e3e1;
    --navy: #163a70;
    --navy-line: #5a6f95;
    --ink: #2b2b2b;
    --paper: #ffffff;
    --grey: #8a8a8a;
  }
  * { box-sizing: border-box; margin: 0; padding: 0; }
  html, body {
    width: 1200px; height: 801px; overflow: hidden;
    background: var(--backdrop);
    font-family: "Lato", Arial, sans-serif;
  }
  .stage {
    width: 1200px; height: 801px;
    display: flex; align-items: center; justify-content: center; gap: 50px;
  }
  .card {
    width: 525px; height: 300px;
    box-shadow: 0 6px 18px rgba(0,0,0,0.18);
    position: relative;
  }
  .card--front { background: var(--paper); display: flex; align-items: center; }
  .card--back {
    background: var(--navy); color: var(--paper);
    display: flex; flex-direction: column; align-items: center; justify-content: center;
  }
  .brand { display: flex; align-items: center; gap: 10px; }
  .brand__dot { border-radius: 50%; flex: none; }
  .brand__name { font-weight: 700; letter-spacing: 0.06em; text-transform: uppercase; }
  .card--front .brand { width: 250px; justify-content: center; }
  .card--front .brand__dot { width: 26px; height: 26px; background: var(--navy); }
  .card--front .brand__name { font-size: 17px; color: var(--navy); }
  .divider { width: 1px; height: 110px; background: var(--navy-line); }
  .contact { padding-left: 32px; color: var(--ink); font-size: 13px; line-height: 1.45; }
  .contact__name { font-size: 19px; font-weight: 700; color: var(--navy); line-height: 1.1; }
  .contact__role { margin-bottom: 14px; }
  .contact__address { margin-bottom: 12px; }
  .contact__line { display: flex; align-items: center; gap: 8px; }
  .contact__line svg { width: 11px; height: 11px; flex: none; }
  .card--back .brand { gap: 16px; }
  .card--back .brand__dot { width: 48px; height: 48px; border: 6px solid var(--paper); }
  .card--back .brand__name { font-size: 34px; color: var(--paper); }
  .card--back .site { margin-top: 34px; font-size: 15px; letter-spacing: 0.08em; }
</style>
</head>
<body>
<main class="stage">
  <section class="card card--front">
    <div class="brand">
      <span class="brand__dot"></span>
      <span class="brand__name">Ward Compass</span>
    </div>
    <div class="divider"></div>
    <div class="contact">
      <p class="contact__name">Salwa Kettani</p>
      <p class="contact__role">CEO</p>
      <p class="contact__address">14 Annakhil 7<br>H.R.B. Rabat, Morocco</p>
      <p class="contact__line">
        <svg viewBox="0 0 12 12" aria-hidden="true"><path d="M2.5 1 L4.5 1 L5 3.5 L3.8 4.4 Q5 7 7.6 8.2 L8.5 7 L11 7.5 L11 9.5 Q10.5 11 9 11 Q1 10 1 2.5 Q1 1 2.5 1Z" fill="#163a70"/></svg>
        +90 612 348 2175
      </p>
      <p class="contact__line">
        <svg viewBox="0 0 12 12" aria-hidden="true"><rect x="0.5" y="2" width="11" height="8" fill="#163a70"/><path d="M0.5 2 L6 6.5 L11.5 2" stroke="#fff" fill="none"/></svg>
        info@wardcompass.example
      </p>
      <p class="contact__line">
        <svg viewBox="0 0 12 12" aria-hidden="true"><circle cx="6" cy="6" r="5.3" fill="#163a70"/><path d="M0.7 6 H11.3 M6 0.7 V11.3 M2 3.3 H10 M2 8.7 H10" stroke="#fff" stroke-width="0.7"/><ellipse cx="6" cy="6" rx="2.4" ry="5.3" stroke="#fff" stroke-width="0.7" fill="none"/></svg>
        www.wardcompass.example
      </p>
    </div>
  </section>

  <section class="card card--back">
    <div class="brand">
      <span class="brand__dot"></span>
      <span class="brand__name">Ward Compass</span>
    </div>
    <p class="site">www.wardcompass.example</p>
  </section>
</main>
</body>
</html>
```